Business cards for Harbourline Supply Pty Ltd that import building products into Australia from China
Target Market(s)
Business to Business
Industry/Entity Type
Business
Contact Information for Business Card
Front: Logo and Business Name
Rear:
Desmond Varrick
General Manager
Mobile: 0427 561 394
email: dessie@harbourlinesupply.com.au
alternative email: dessie@outbackworks.com.au
web: www.harbourlinesupply.com.au
Adelaide, Brisbane and Darwin
Colors
ec1f27
fbee3d

```html
<!DOCTYPE html>
<html lang="en">
<head>
<meta charset="utf-8">
<title>Harbourline Supply Pty Ltd – Business Cards</title>
<link rel="stylesheet" href="https://fonts.googleapis.com/css2?family=Rubik:wght@400;500;700&display=swap">
<style>
  :root {
    --brand-red: #ec1f27;
    --brand-yellow: #fbee3d;
    --band-yellow: #ecdc1c;
    --ink: #1e1e1e;
    --paper: #ffffff;
    --stage: #000000;
  }
  * { margin: 0; padding: 0; box-sizing: border-box; }
  html, body {
    width: 1200px; height: 900px; overflow: hidden;
    background: var(--stage);
    font-family: "Rubik", Arial, sans-serif;
  }
  .stage { position: relative; width: 1200px; height: 900px; }

  .card {
    position: absolute; top: 271px;
    width: 457px; height: 281px;
    border-radius: 12px; overflow: hidden;
  }
  .card--contact { left: 137px; background: var(--paper); }
  .card--brand { left: 626px; background: var(--brand-yellow); }

  .person { position: absolute; left: 26px; top: 25px; }
  .person__name {
    font-size: 19px; font-weight: 700; letter-spacing: 0.3px;
    color: var(--ink); line-height: 1;
  }
  .person__first { color: var(--brand-red); }
  .person__role { margin-top: 7px; font-size: 12.5px; color: var(--ink); }

  .wordmark {
    position: absolute; display: flex; align-items: center; gap: 8px;
    font-weight: 700; color: var(--ink); line-height: 1.05;
  }
  .wordmark__square { background: var(--brand-red); flex: none; }
  .wordmark--front { right: 34px; top: 60px; font-size: 19px; }
  .wordmark--front .wordmark__square { width: 26px; height: 26px; }
  .wordmark--back {
    left: 0; right: 0; top: 112px; justify-content: center;
    font-size: 26px; gap: 12px;
  }
  .wordmark--back .wordmark__square { width: 36px; height: 36px; }

  .contacts {
    position: absolute; left: 26px; top: 183px; list-style: none;
    font-size: 12.8px; color: var(--ink);
  }
  .contacts li { display: flex; align-items: center; height: 19px; gap: 9px; }
  .contacts svg { width: 12px; height: 12px; fill: var(--brand-red); flex: none; }

  .locations {
    position: absolute; right: 34px; top: 218px;
    font-size: 12.8px; color: var(--ink); text-align: right; line-height: 21px;
  }

  .band { position: absolute; bottom: 0; height: 14px; }
  .band--red { left: 0; width: 218px; background: var(--brand-red); }
  .band--yellow { left: 226px; right: 0; background: var(--band-yellow); }

  .brand-field { position: absolute; inset: 0; background: var(--brand-yellow); }
</style>
</head>
<body>
<main class="stage">

  <section class="card card--contact" aria-label="Business card contact side">
    <div class="person">
      <p class="person__name"><span class="person__first">DESMOND</span> VARRICK</p>
      <p class="person__role">General Manager</p>
    </div>

    <div class="wordmark wordmark--front">
      <span class="wordmark__square"></span>
      <span>Harbourline Supply<br>Pty Ltd</span>
    </div>

    <ul class="contacts">
      <li>
        <svg viewBox="0 0 12 12" aria-hidden="true"><path d="M1 4c0-1.5 2-3 5-3s5 1.5 5 3v1H8.5V3.8h-5V5H1z M2.5 6h7l1 5h-9z M4.5 7.5h3v2h-3z" fill-rule="evenodd"/></svg>
        <span>0427 561 394</span>
      </li>
      <li>
        <svg viewBox="0 0 12 12" aria-hidden="true"><path d="M1 2.5h10v7H1z M1.8 3.3 6 6.5l4.2-3.2v.9L6 7.4 1.8 4.2z" fill-rule="evenodd"/></svg>
        <span>dessie@harbourlinesupply.com.au</span>
      </li>
      <li>
        <svg viewBox="0 0 12 12" aria-hidden="true"><path d="M1 2.5h10v7H1z M1.8 3.3 6 6.5l4.2-3.2v.9L6 7.4 1.8 4.2z" fill-rule="evenodd"/></svg>
        <span>dessie@outbackworks.com.au</span>
      </li>
      <li>
        <svg viewBox="0 0 12 12" aria-hidden="true"><circle cx="6" cy="6" r="5.2"/><path d="M3.5 3.5c1 .2 1.5 1 1 1.8s.8 1.2 1.5 2-.2 2-.6 2.6M8 2.6c-.4.8 0 1.4.8 1.6" stroke="#fff" stroke-width="1" fill="none"/></svg>
        <span>www.harbourlinesupply.com.au</span>
      </li>
    </ul>

    <p class="locations">Adelaide,<br>Brisbane and Darwin</p>

    <span class="band band--red"></span>
    <span class="band band--yellow"></span>
  </section>

  <section class="card card--brand" aria-label="Business card brand side">
    <div class="brand-field" role="img" aria-label="Faint repeating brand pattern on yellow"></div>
    <div class="wordmark wordmark--back">
      <span class="wordmark__square"></span>
      <span>Harbourline Supply<br>Pty Ltd</span>
    </div>
  </section>

</main>
</body>
</html>
```